Business Card Design Project

We are not a new company, but renamed to "Vantorin Kitchens" last year. We specialize in modern high-end cabinetry imports. We would like to communicate a sense of quality and cutting edge technology. Ideally the design would incorporate our logo colors, silver, red and preferably a black, matte background. Though we are open to suggestions.
Logo is attached.
Edit: I have attached rough drafts of the previous cards, this way you will have all necessary content that needs to go on the cards.
Updates
Project Deadline Extended
Reason: We have received a lot of great designs, but due to the sheer number we couldn't respond to all. We will extend the deadline for another 7 days to finalize and provide feedback to designers.
Thank you for your hard work!
Industry/Entity Type
Business
Look and feel
Each slider illustrates characteristics of the customer's brand and the style your logo design should communicate.

```html
<!DOCTYPE html>
<html lang="en">
<head>
<meta charset="utf-8">
<title>Vantorin Kitchens — Business Card</title>
<link rel="stylesheet" href="https://fonts.googleapis.com/css2?family=Arimo:wght@400;700&display=swap">
<style>
  :root {
    --backdrop: #c9d3d2;
    --matte-black: #050505;
    --brand-red: #e31b23;
    --silver-light: #e4e4e4;
    --silver-mid: #b9b9b9;
    --silver-dark: #8f8f8f;
    --logo-silver: #c4c4c4;
    --ink-white: #ffffff;
    --ink-dark: #ffffff;
  }
  * { box-sizing: border-box; margin: 0; padding: 0; }
  html, body {
    width: 1200px; height: 973px; overflow: hidden;
    background: var(--backdrop);
    font-family: "Arimo", Arial, sans-serif;
  }
  .canvas { position: relative; width: 1200px; height: 973px; }
  .card {
    position: absolute; left: 250px; width: 700px; height: 400px;
    background: var(--matte-black); overflow: hidden;
    box-shadow: 0 6px 18px rgba(0,0,0,.22);
  }
  .card--front { top: 62px; }
  .card--back { top: 511px; }
  .card__bg { position: absolute; inset: 0; }

  .wordmark {
    position: absolute; display: flex; align-items: center; gap: 14px;
    color: var(--logo-silver); font-weight: 700; letter-spacing: 2px;
    text-transform: uppercase; white-space: nowrap;
  }
  .wordmark__square { width: 30px; height: 30px; background: var(--logo-silver); }
  .card--front .wordmark { left: 40px; top: 120px; font-size: 30px; }
  .card--back .wordmark { left: 50%; top: 50%; transform: translate(-50%, -50%); font-size: 40px; }
  .card--back .wordmark__square { width: 40px; height: 40px; }

  .person { position: absolute; left: 40px; top: 232px; color: var(--ink-white); }
  .person__name { font-size: 17px; font-weight: 400; letter-spacing: .5px; }
  .person__role { font-size: 15px; font-weight: 700; color: var(--brand-red); margin-top: 3px; }
  .address { position: absolute; left: 40px; top: 310px; color: var(--ink-white); font-size: 15px; line-height: 1.35; font-style: normal; }

  .contact {
    position: absolute; right: 28px; top: 128px; list-style: none;
    color: var(--ink-dark); font-size: 15px; text-align: right;
    text-shadow: 0 1px 1px rgba(0,0,0,.25);
  }
  .contact li { display: flex; justify-content: flex-end; align-items: center; gap: 7px; margin-bottom: 6px; }
  .contact li.contact__email { margin-top: 44px; }
  .contact svg { width: 13px; height: 13px; fill: var(--ink-dark); }
</style>
</head>
<body>
<main class="canvas">

  <section class="card card--front" aria-label="Business card front">
    <svg class="card__bg" viewBox="0 0 700 400" preserveAspectRatio="none" aria-hidden="true">
      <defs>
        <linearGradient id="silverPanel" x1="0" y1="0" x2="1" y2="1">
          <stop offset="0" stop-color="var(--silver-light)"/>
          <stop offset=".55" stop-color="var(--silver-mid)"/>
          <stop offset="1" stop-color="var(--silver-dark)"/>
        </linearGradient>
      </defs>
      <rect width="700" height="400" fill="var(--matte-black)"/>
      <path d="M455 0 Q500 250 300 400 L700 400 L700 0 Z" fill="var(--brand-red)"/>
      <path d="M525 0 Q540 260 335 400 L700 400 L700 0 Z" fill="url(#silverPanel)"/>
    </svg>

    <div class="wordmark"><span class="wordmark__square"></span>Vantorin Kitchens</div>

    <div class="person">
      <p class="person__name">MAREK DELVANO</p>
      <p class="person__role">Director</p>
    </div>
    <address class="address">1208 - 45 Ave. Calgary<br>AB T2K 4R9</address>

    <ul class="contact">
      <li><svg viewBox="0 0 16 16"><path d="M3 1l3 3-1.5 2a9 9 0 0 0 5.5 5.5L12 10l3 3-2 2C7 15 1 9 1 3z"/></svg>780.555.0142</li>
      <li><svg viewBox="0 0 16 16"><path d="M4 2h7v4H4zM1 7h14v6h-3v2H4v-2H1z"/></svg>780.555.0187</li>
      <li><svg viewBox="0 0 16 16"><path d="M4 0h8v16H4zM6 2v10h4V2z"/></svg>780.555.0163</li>
      <li class="contact__email"><svg viewBox="0 0 16 16"><path d="M1 3h14v10H1zM2 4l6 5 6-5z"/></svg>marek@vantorinkitchens.ca</li>
    </ul>
  </section>

  <section class="card card--back" aria-label="Business card back">
    <div class="wordmark"><span class="wordmark__square"></span>Vantorin Kitchens</div>
  </section>

</main>
</body>
</html>
```